Skincare Clinic specializing in treating difficult skin conditions needs a web design

We want to restructure and rehash our current webdesigns. The current ones are dated and look very old fashioned also, they are not structured well.

The current websites need to get an uplift in look and become more classy and modern with navigation ease by structuring the information into ease of access

The current web address is
www.brightdermhaven.com.au and
www.lumacutis.com.au

We also have international Partner website which is good and we need to better than them. So this website will act as a guide to better the new site
www.dermacalm-drtorvelle.com

But the new site should be more inclined towards a Blue colour or Aqua marine blue orientation and it needs to be Scientific giving authenticity to the medical industry we operate in.

Attached is a webdesign framework and architecture we would want to adopt. It is a schematic diagram and you can creatively adopt based on what you want to propose.

The website needs to be coded and Should be coded in WordPress such that it helps with SEO activity and nexora promoline pickup.

We will need the necessary pictures and we could provide them or agree to by them from the designers source.

Target Market(s)

Patients with Skin Disease and people interested to book consultation or buy products for their Skin condition

Industry/Entity Type

Clinic

Coding

Coded - Design and coding required

Number of Pages Required

5+ page

Font styles to use
Other font styles liked:
• Use a light font denoting class.

Requirements
Must have
• Should be modern, Easy to navigate, mobile friendly and coded in wordpress
• Blue colour and should look scientific and medicinal
Nice to have
• Classy and creative
Should not have
• No Green colour or herbal look

```html
<!DOCTYPE html>
<html lang="en">
<head>
<meta charset="utf-8">
<title>brightdermhaven — Clearleaf Skin Clinic</title>
<link rel="stylesheet" href="https://fonts.googleapis.com/css2?family=Montserrat:wght@300;400;500&family=Libre+Baskerville:ital@1&family=Mulish:ital,wght@0,400;1,400&display=swap">
<style>
:root{
  --blue:#1d8fe1;
  --blue-deep:#1a7cc8;
  --navy:#1d5b86;
  --panel:#c6ebfb;
  --teal:#7dbfc5;
  --ink:#2b2b2b;
  --white:#ffffff;
  --hero-a:#d9d9db;
  --hero-b:#b9a9ac;
}
*{box-sizing:border-box;margin:0;padding:0}
html,body{width:919px;height:1200px;overflow:hidden;background:var(--white)}
body{position:relative;font-family:"Mulish",sans-serif;color:var(--ink)}
.abs{position:absolute}
.top-rule{left:0;top:0;width:919px;height:4px;background:var(--blue)}
.brand{left:58px;top:38px;display:flex;align-items:center;gap:8px}
.brand-text{font-family:"Montserrat",sans-serif;font-weight:500;color:var(--blue);font-size:20px;line-height:1;letter-spacing:-.5px}
.brand-sub{font-family:"Montserrat",sans-serif;font-weight:500;color:var(--blue);font-size:10px;margin-top:3px;letter-spacing:0}
.brand-dot{width:30px;height:30px;border-radius:50%;background:var(--blue)}
.mission{left:505px;top:18px;width:357px;height:75px;background:var(--panel);padding:10px 18px 0 34px;font-family:"Libre Baskerville",serif;font-style:italic;font-size:11.3px;line-height:18.5px;color:#333}
.mission .q{position:absolute;font-family:"Libre Baskerville",serif;color:var(--blue);font-size:22px;font-style:normal;font-weight:bold}
.nav{left:57px;top:106px;width:805px;height:35px;background:var(--blue)}
.nav a{position:absolute;top:0;height:35px;line-height:37px;color:var(--white);font-family:"Montserrat",sans-serif;font-size:9.8px;text-decoration:none}
.nav .active{background:var(--teal);padding:0 21px}
.dropdown{left:126px;top:141px;width:165px;height:124px;background:var(--teal);padding:8px 0 0 16px;list-style:none;box-shadow:2px 2px 4px rgba(0,0,0,.15);z-index:3}
.dropdown li{font-family:"Montserrat",sans-serif;font-size:8.6px;color:var(--white);line-height:16.3px}
.dropdown li::before{content:"»";margin-right:6px;font-size:8px}
.hero{left:57px;top:141px;width:805px;height:318px;background:linear-gradient(90deg,var(--hero-a) 0%,#d4d0d2 45%,#9d6f72 62%,#5b3e3a 80%,#a9989b 100%)}
.hero-title{left:77px;top:200px;font-family:"Montserrat",sans-serif;font-weight:400;font-size:36px;line-height:41px;color:var(--blue-deep)}
.hero-sub{left:77px;top:287px;font-family:"Montserrat",sans-serif;font-size:20.5px;color:#222}
.hero-btn{left:78px;top:340px;width:123px;height:37px;background:var(--panel);color:var(--blue-deep);font-family:"Montserrat",sans-serif;font-size:13px;text-align:center;line-height:38px}
.card{top:477px;width:253px;height:185px;border-bottom:5px solid var(--blue)}
.card .photo{width:100%;height:100%}
.card-label{position:absolute;left:0;bottom:0;width:165px;height:48px;background:var(--blue);padding:9px 0 0 13px;color:var(--white);font-family:"Montserrat",sans-serif}
.card-label b{display:block;font-weight:400;font-size:16px;line-height:18px}
.card-label span{display:block;font-size:12px;line-height:16px;color:#111}
.panel{background:var(--panel)}
.panel h2{font-family:"Montserrat",sans-serif;font-weight:400;color:var(--blue);font-size:18px;line-height:23px}
.panel h2 em{font-style:normal;color:var(--navy)}
.panel p{font-size:9.2px;line-height:16.3px;color:#222}
.btn{display:inline-block;background:var(--blue);color:var(--white);font-family:"Montserrat",sans-serif;font-size:8.8px;padding:0 14px;height:25px;line-height:26px}
.case{position:absolute;left:16px;width:360px;height:64px}
.case .thumb{position:absolute;left:0;top:0;width:114px;height:64px;background:linear-gradient(90deg,#c9938f 0%,#b98680 48%,#d2b39a 52%,#c89c7e 100%)}
.case h3{position:absolute;left:128px;top:-2px;font-family:"Montserrat",sans-serif;font-weight:400;font-size:11.5px}
.case p{position:absolute;left:128px;top:16px;width:240px;font-size:8.6px;line-height:14px}
.case .more{position:absolute;left:128px;font-family:"Montserrat",sans-serif;font-size:8.8px}
.testimonial{position:absolute;left:16px;width:370px;height:58px}
.testimonial .avatar{position:absolute;left:0;top:0;width:57px;height:57px;background:linear-gradient(180deg,#8a6e5c,#c99a84 55%,#6e5a5a)}
.testimonial p{position:absolute;left:70px;top:-2px;width:300px;font-style:italic;font-size:8.9px;line-height:16.3px}
.testimonial .who{position:absolute;left:70px;top:49px;font-size:8.9px}
.footer{left:0;top:1126px;width:919px;height:74px;background:var(--blue);color:var(--white)}
.footer .legal{position:absolute;left:57px;top:22px;font-family:"Montserrat",sans-serif;font-size:9px;line-height:16.3px;color:#d7efff}
.footer .legal b{font-weight:400;color:#111}
.footer .connect{position:absolute;left:661px;top:32px;font-family:"Montserrat",sans-serif;font-size:9.2px}
.footer .social{position:absolute;left:738px;top:25px;display:flex;gap:4px}
.footer .social span{width:23px;height:23px;border-radius:50%;background:var(--white)}
</style>
</head>
<body>
<div class="abs top-rule"></div>

<header>
  <div class="abs brand">
    <div>
      <div class="brand-text">brightdermhaven</div>
      <div class="brand-sub">by Clearleaf Skin Clinic</div>
    </div>
    <div class="brand-dot"></div>
  </div>
  <blockquote class="abs mission">
    <span class="q" style="left:10px;top:6px">“</span>
    We are commotted to ongoing research to bring you the best possible treatment protocaols in Complementary Dermatology...
    <span class="q" style="left:219px;top:50px">”</span>
  </blockquote>
</header>

<nav class="abs nav">
  <a style="left:16px">HOME</a>
  <a class="active" style="left:69px">ABOUT US</a>
  <a style="left:186px">TREATMENTS&nbsp; PROTOCOL</a>
  <a style="left:358px">PRODUCTS</a>
  <a style="left:457px">RESULTS</a>
  <a style="left:544px">MEDIA</a>
  <a style="left:620px">SKIN CONDITIONS</a>
</nav>

<section>
  <div class="abs hero" role="img" aria-label="Photo of a young woman touching her itchy cheek"></div>
  <h1 class="abs hero-title">Itchy &amp; free of<br>your Psoriasis?</h1>
  <p class="abs hero-sub">Your Future is clear with us, Naturally.</p>
  <div class="abs hero-btn">READ MORE</div>
  <ul class="abs dropdown">
    <li>Introduction</li>
    <li>History</li>
    <li>Our Founder</li>
    <li>Our Treatment Protocol</li>
    <li>Our Logo</li>
    <li>International Partnership</li>
    <li>Contact Details</li>
  </ul>
</section>

<section>
  <div class="abs card" style="left:57px">
    <div class="photo" role="img" aria-label="Photo of the clinic founder in a white coat" style="background:linear-gradient(90deg,#e6d8c4,#b89a85 40%,#e9ddd0 70%,#d8c7b4)"></div>
    <div class="card-label"><b>CONSULTATION</b><span>BOOK ONLINE</span></div>
  </div>
  <div class="abs card" style="left:333px">
    <div class="photo" role="img" aria-label="Photo of the clinic's skincare product bottles" style="background:linear-gradient(180deg,#f1f1f1,#dcdcdc 60%,#c9c5bd)"></div>
    <div class="card-label"><b>PURCHASE</b><span>PRODUCTS ONLINE</span></div>
  </div>
  <div class="abs card" style="left:609px">
    <div class="photo" role="img" aria-label="Photo of a doctor consulting with a patient" style="background:linear-gradient(90deg,#c8d8df,#6fa6ad 35%,#e8eef0 60%,#aebfc2)"></div>
    <div class="card-label"><b>PRACTITIONERS</b><span>INTRANET ACCESS</span></div>
  </div>
</section>

<section class="abs panel" style="left:57px;top:680px;width:392px;height:207px;padding:17px 16px">
  <h2>ABOUT<br><em>DR ELIAS MARROW</em></h2>
  <p style="width:245px;margin-top:4px">Lorem ipsum dolor sit amet, consect- etuer adipiscing elit, sed diam nonummy nibh euismod tincidunt ut laoreet dolore magna aliquam erat&nbsp; volutpat. Ut wisi enim ad minim veniam, quis nostrud exerci tation ullam. Consectetuer adipiscing elit, sed diam nonummy nibh euismod...</p>
  <div class="btn" style="margin-top:9px">READ MORE</div>
</section>

<section class="abs panel" style="left:470px;top:676px;width:392px;height:208px">
  <h2 style="position:absolute;left:16px;top:21px">CASE <em>STUDIES</em></h2>
  <svg class="abs" style="left:347px;top:24px" width="34" height="14" viewBox="0 0 34 14" aria-label="Previous and next">
    <path d="M7 1 L1 7 L7 13" fill="none" stroke="var(--blue)" stroke-width="1.5"/>
    <path d="M27 1 L33 7 L27 13" fill="none" stroke="#222" stroke-width="1.5"/>
  </svg>
  <div class="case" style="top:52px">
    <div class="thumb" role="img" aria-label="Before and after photos of psoriasis on the back"></div>
    <h3>Heading Title</h3>
    <p>Lorem ipsum dolor sit amet, consect- etuer adipiscing elit, sed diam nonummy nibh euismod....</p>
    <span class="more" style="top:50px">LEARN MORE</span>
  </div>
  <div class="case" style="top:133px">
    <div class="thumb" role="img" aria-label="Before and after photos of facial skin treatment"></div>
    <h3>Heading Title</h3>
    <p>Lorem ipsum dolor sit amet, consect- etuer adipiscing elit, sed diam nonummy nibh euismod....</p>
    <span class="more" style="top:55px">LEARN MORE</span>
  </div>
</section>

<section class="abs panel" style="left:57px;top:900px;width:392px;height:208px;padding:16px 16px">
  <h2>WHAT’S UNIQUE ABOUT OUR<br>TREATMENT PROTOCOLS</h2>
  <p style="margin-top:9px">Lorem ipsum dolor sit amet, consect- etuer adipiscing elit, sed diam nonummy nibh euismod tincidunt ut laoreet dolore magna aliquam erat&nbsp; volutpat. Ut wisi enim ad minim veniam, quis nostrud exerci tation ullam. Consectetuer adipiscing elit, sed diam nonummy nibh euismod. Magna aliquam erat volut- pat. Ut wisi enim ad minim veniam, quis nostrud exerci tation ullam.</p>
  <div class="btn" style="margin-top:13px">READ MORE</div>
</section>

<section class="abs panel" style="left:470px;top:900px;width:392px;height:208px">
  <h2 style="position:absolute;left:16px;top:16px">OUR <em>TESTIMONIALS</em></h2>
  <div class="testimonial" style="top:52px">
    <div class="avatar" role="img" aria-label="Portrait of a patient"></div>
    <p>Lorem ipsum dolor sit amet, consect- etuer adipiscing elit, sed diam nonummy nibh euismod tincidunt ut laoreet dolore magna aliquam erat&nbsp; volutpat. ...</p>
    <span class="who">-Name Goes Here</span>
  </div>
  <div class="testimonial" style="top:133px">
    <div class="avatar" role="img" aria-label="Portrait of a patient"></div>
    <p>Lorem ipsum dolor sit amet, consect- etuer adipiscing elit, sed diam nonummy nibh euismod tincidunt ut laoreet dolore magna aliquam erat&nbsp; volutpat. ...</p>
    <span class="who">-Name Goes Here</span>
  </div>
</section>

<footer class="abs footer">
  <div class="legal">Copyright © 2015.<b>Company Name</b>.All Right Reserved<br>Privacy Policy&nbsp; |&nbsp;&nbsp; Term of Services</div>
  <div class="connect">CONNECT US:</div>
  <div class="social" aria-label="Social links">
    <span></span><span></span><span></span><span></span><span></span>
  </div>
</footer>
</body>
</html>
```